Business card design needed

I run a Beautician studio (for 7 years now)
I offer
- Velmo Body Sugaring
- Ruby Glaze
- Nails
- Facials
- Manicure
- Foot Treatment
It might not be necessary to list all those treatments?
Maybe the link to the Website is sufficient?
I leave that up to you ...
(more info on www.FernAndDewByLenka.com.au)
Velmo BodySugaring is our biggest success, It replaces waxing.
I would like to incorporate the logo into the Business Card.
We had many complaints regarding our old Business Cards as the Phone Number was to small.
On the backside, we would like a "your next Appointment" section.
Looking forward to you Design, cheers ... Lenka
Industry/Entity Type
Business
Contact Information for Business Card
Fern by Dew by Lenka
14 Korrin Sqr 3942 Berwick
www.FernAndDewByLenka.com.au
03 9481 2267

```html
<!DOCTYPE html>
<html lang="en">
<head>
<meta charset="utf-8">
<title>Fern &amp; Dew by Lenka — Business Card</title>
<link href="https://fonts.googleapis.com/css2?family=Ubuntu:wght@400;500&family=Source+Sans+3:ital,wght@0,400;0,700;1,700&family=Tinos&display=swap" rel="stylesheet">
<style>
  :root {
    --backdrop: #e9e6e2;
    --card: #ffffff;
    --ink: #3d3d3d;
    --ink-soft: #555555;
    --rule: #9a9a9a;
    --swoosh-dark: #5c5c5c;
    --swoosh-light: #b5b5b5;
    --brand: #e38a1e;
    --brand-faint: rgba(227, 138, 30, 0.12);
  }
  * { box-sizing: border-box; margin: 0; padding: 0; }
  html, body { width: 1200px; height: 788px; overflow: hidden; }
  body {
    position: relative;
    background: var(--backdrop);
    font-family: "Source Sans 3", sans-serif;
    color: var(--ink);
  }
  .side-label {
    position: absolute;
    font-family: "Source Sans 3", sans-serif;
    font-size: 22px;
    color: #222;
    transform: translateX(-50%);
  }
  .card {
    position: absolute;
    width: 524px;
    height: 299px;
    background: var(--card);
    border-radius: 22px;
    overflow: hidden;
    box-shadow: 0 4px 12px rgba(0,0,0,0.25);
  }
  .card > * { position: absolute; }
  .card--front { left: 338px; top: 75px; }
  .card--back-one { left: 54px; top: 444px; }
  .card--back-two { left: 622px; top: 444px; }

  .swoosh { left: 0; top: 0; width: 524px; height: 299px; }

  .brand-mark { display: flex; align-items: center; gap: 8px; }
  .brand-mark__dot { width: 16px; height: 16px; border-radius: 50%; background: var(--brand); }
  .brand-mark__name {
    font-family: "Ubuntu", sans-serif;
    font-weight: 500;
    font-size: 15px;
    color: var(--brand);
    white-space: nowrap;
  }
  .card--front .brand-mark { left: 0; width: 100%; top: 95px; justify-content: center; }

  .studio-name {
    font-family: "Ubuntu", sans-serif;
    font-weight: 400;
    color: var(--ink);
    white-space: nowrap;
  }
  .card--front .studio-name { left: 0; width: 100%; top: 160px; text-align: center; font-size: 36px; letter-spacing: 0.5px; }

  .contact { left: 0; width: 100%; text-align: center; font-size: 17px; color: var(--ink); }
  .contact b { font-style: italic; font-weight: 700; }
  .contact--line-one { top: 221px; }
  .contact--line-two { top: 250px; }

  /* Back one */
  .card--back-one .studio-name { left: 0; width: 100%; top: 12px; text-align: center; font-size: 26px; }
  .header-rule { left: 0; top: 50px; width: 100%; height: 1px; background: #777; }
  .faint-brand {
    left: 120px; top: 176px;
    font-family: "Ubuntu", sans-serif;
    font-size: 58px;
    letter-spacing: 8px;
    color: var(--brand-faint);
  }
  .section-title { font-style: italic; font-weight: 700; font-size: 18px; color: var(--ink); }
  .offer-title { left: 29px; top: 68px; }
  .offer-list { left: 30px; top: 97px; list-style: none; font-family: "Tinos", serif; font-size: 15px; color: var(--ink-soft); }
  .offer-list li { height: 20px; }
  .offer-list li::before { content: "▪"; font-size: 10px; margin-right: 6px; position: relative; top: -2px; }
  .column-rule { left: 207px; top: 83px; width: 2px; height: 130px; background: linear-gradient(var(--rule), #d0d0d0); }
  .appointment-title { left: 243px; top: 68px; }
  .fill-line { display: flex; align-items: flex-end; font-size: 17px; color: var(--ink); }
  .fill-line__blank { border-bottom: 1px solid #555; height: 18px; margin-left: 2px; }
  .fill-line--name { left: 243px; top: 109px; }
  .fill-line--date { left: 243px; top: 149px; }
  .fill-line--time { left: 243px; top: 189px; }
  .hours-title { left: 0; width: 100%; text-align: center; top: 237px; font-size: 15px; font-style: italic; font-weight: 700; }
  .hours-compact { left: 60px; top: 260px; font-size: 13.5px; white-space: nowrap; }
  .hours-compact span + span { margin-left: 44px; }

  /* Back two */
  .card--back-two .hours-heading { left: 32px; top: 27px; font-size: 21px; letter-spacing: 1.5px; }
  .hours-full { left: 29px; top: 60px; font-size: 18.5px; line-height: 24px; color: var(--ink); }
  .card--back-two .brand-mark { left: 382px; top: 76px; }
  .back-rule { left: 28px; top: 116px; width: 468px; height: 1px; background: #c8c8c8; }
  .appointment-holder { left: 45px; top: 143px; }
  .appointment-date { left: 34px; top: 192px; }
  .fill-line .gap { margin: 0 8px; }
  .weekdays { left: 58px; top: 246px; display: flex; gap: 26px; font-size: 18px; align-items: center; }
  .weekday { display: flex; align-items: center; gap: 8px; }
  .weekday__box { width: 22px; height: 22px; border: 1px solid #444; }
</style>
</head>
<body>

<div class="side-label" style="left:600px; top:33px;">Front</div>
<section class="card card--front">
  <svg class="swoosh" viewBox="0 0 524 299" aria-hidden="true">
    <path d="M430 0 Q505 6 524 52 L524 26 Q515 4 470 0 Z" fill="var(--swoosh-light)"/>
    <path d="M455 0 Q510 8 524 36 L524 16 Q515 2 490 0 Z" fill="var(--swoosh-dark)"/>
    <path d="M0 255 Q40 290 110 299 L60 299 Q15 290 0 275 Z" fill="var(--swoosh-light)"/>
    <path d="M0 268 Q30 292 80 299 L45 299 Q12 293 0 283 Z" fill="var(--swoosh-dark)"/>
  </svg>
  <div class="brand-mark"><span class="brand-mark__dot"></span><span class="brand-mark__name">Velmo Body Sugaring</span></div>
  <h1 class="studio-name">FERN&amp;DEW BY LENKA</h1>
  <p class="contact contact--line-one"><b>phone</b> 03 9481 2267 &nbsp;|&nbsp; <b>add</b> 14 Korrin Sqr, 3942 Berwick</p>
  <p class="contact contact--line-two"><b>web</b> www.FernAndDewByLenka.com.au</p>
</section>

<div class="side-label" style="left:323px; top:402px;">Back - 1</div>
<section class="card card--back-one">
  <div class="faint-brand" aria-hidden="true">VELMO</div>
  <h2 class="studio-name">FERN&amp;DEW BY LENKA</h2>
  <div class="header-rule"></div>
  <h3 class="section-title offer-title">I offer</h3>
  <ul class="offer-list">
    <li>Velmo Body Sugaring</li>
    <li>Ruby Glaze</li>
    <li>Nails</li>
    <li>Facials</li>
    <li>Manicure</li>
    <li>Foot Treatment</li>
  </ul>
  <div class="column-rule"></div>
  <h3 class="section-title appointment-title">An Appointment</h3>
  <div class="fill-line fill-line--name">Name<span class="fill-line__blank" style="width:218px"></span></div>
  <div class="fill-line fill-line--date">Date<span class="fill-line__blank" style="width:225px"></span></div>
  <div class="fill-line fill-line--time">time<span class="fill-line__blank" style="width:160px"></span>&nbsp;am / pm</div>
  <p class="hours-title">Hours of Operation</p>
  <p class="hours-compact"><span>Mon. to Fri.&nbsp; 7.30am - 7.00pm</span><span>Sat. 7.30am - 12.00pm</span></p>
</section>

<div class="side-label" style="left:897px; top:402px;">Back - 2</div>
<section class="card card--back-two">
  <h3 class="section-title hours-heading">Hours of Operation</h3>
  <p class="hours-full">Monday to Friday -&nbsp; 7.30am - 7.00pm<br>Saturday - 7.30am - 12.00pm</p>
  <div class="brand-mark"><span class="brand-mark__dot"></span><span class="brand-mark__name">Velmo</span></div>
  <div class="back-rule"></div>
  <div class="fill-line appointment-holder"><span class="fill-line__blank" style="width:260px; margin:0 4px 0 0"></span>has an appointment</div>
  <div class="fill-line appointment-date">Date :<span class="fill-line__blank" style="width:42px"></span><span class="gap">/</span><span class="fill-line__blank" style="width:42px"></span><span class="gap">/</span><span class="fill-line__blank" style="width:52px"></span><span class="gap">@</span><span class="fill-line__blank" style="width:42px"></span><span class="gap">:</span><span class="fill-line__blank" style="width:52px"></span>am / pm</div>
  <div class="weekdays">
    <span class="weekday"><span class="weekday__box"></span>Mon.</span>
    <span class="weekday"><span class="weekday__box"></span>Tue.</span>
    <span class="weekday"><span class="weekday__box"></span>Wed.</span>
    <span class="weekday"><span class="weekday__box"></span>Thu.</span>
    <span class="weekday"><span class="weekday__box"></span>Fri.</span>
  </div>
</section>

</body>
</html>
```